Business Card Design Project - 2 sided

We need a business card design for a card having one business on each side (ie. two businesses on one card). Would like a design that incorporates logo, tagline and normal fields (name, position, address, phone).

Would also like an allowance for small font text along the bottom (text to be determined, but less than 50 characters).

NB. Attached logo for Harbor Quill has two variations - either can be used.

www.harborquill-example.com / www.velmaro-example.com

```html
<!DOCTYPE html>
<html lang="en">
<head>
<meta charset="utf-8">
<title>Harbor Quill – Business Card</title>
<link rel="stylesheet" href="https://fonts.googleapis.com/css2?family=Open+Sans:wght@400;600;700&display=swap">
<style>
  :root {
    --page-bg: #ecebe8;
    --card-bg: #ffffff;
    --accent-green: #8dc63f;
    --text-grey: #4d4d4d;
    --muted-grey: #6d6d6d;
    --divider: #c8c8c8;
  }
  * { box-sizing: border-box; margin: 0; padding: 0; }
  html, body {
    width: 1200px; height: 487px; overflow: hidden;
    background: var(--page-bg);
    font-family: "Open Sans", Arial, sans-serif;
  }
  .sheet { position: relative; width: 1200px; height: 487px; }
  .card {
    position: absolute; top: 89px;
    width: 541px; height: 308px;
    background: var(--card-bg);
    border-radius: 16px;
    border: 1px solid #dcdcdc;
  }
  .card--front { left: 47px; }
  .card--back { left: 611px; }

  .brand {
    position: absolute; left: 40px; top: 150px; width: 250px;
  }
  .brand__name {
    display: flex; align-items: center; gap: 8px;
    font-size: 20px; font-weight: 600;
    color: var(--text-grey);
  }
  .brand__mark {
    width: 12px; height: 12px; border-radius: 50%;
    background: var(--text-grey); flex: none;
  }
  .brand__tagline {
    margin-top: 4px; font-size: 8.5px; color: var(--text-grey);
    white-space: nowrap;
  }

  .divider {
    position: absolute; left: 300px; top: 66px;
    width: 1px; height: 170px;
    background: linear-gradient(to bottom, transparent, var(--divider) 20%, var(--divider) 80%, transparent);
  }

  .contact { position: absolute; left: 322px; top: 62px; color: var(--text-grey); }
  .contact__name { font-size: 17px; font-weight: 700; color: var(--accent-green); }
  .contact__title { font-size: 13px; font-weight: 400; color: var(--accent-green); }
  .contact__list { list-style: none; margin-top: 14px; }
  .contact__item {
    display: flex; align-items: center; gap: 5px;
    font-size: 13.5px; line-height: 18px;
  }
  .contact__icon { width: 10px; height: 10px; flex: none; fill: var(--accent-green); }
  .contact__address { margin-top: 12px; font-size: 13.5px; line-height: 18px; }

  .fine-print {
    position: absolute; left: 95px; top: 260px;
    font-size: 12.5px; letter-spacing: 0.1px; color: var(--muted-grey);
    white-space: nowrap;
  }
</style>
</head>
<body>
<svg width="0" height="0" style="position:absolute" aria-hidden="true">
  <symbol id="icon-phone" viewBox="0 0 10 10"><path d="M2 1l2 2-1 1c.5 1.2 1.5 2.2 2.7 2.7l1-1 2 2-1.3 1.3C4.5 8.6 1.4 5.5.7 2.3z"/></symbol>
  <symbol id="icon-mobile" viewBox="0 0 10 10"><rect x="2.5" y="0" width="5" height="10" rx="1"/><rect x="3.3" y="1.2" width="3.4" height="6" fill="#fff"/></symbol>
  <symbol id="icon-fax" viewBox="0 0 10 10"><path d="M1 3h8v5H1z"/><rect x="3" y="1" width="4" height="2"/><rect x="3" y="5" width="4" height="1" fill="#fff"/></symbol>
  <symbol id="icon-mail" viewBox="0 0 10 10"><rect x="0" y="2" width="10" height="6.5" rx="1"/><path d="M.5 2.5L5 6l4.5-3.5" stroke="#fff" stroke-width="1" fill="none"/></symbol>
  <symbol id="icon-web" viewBox="0 0 10 10"><circle cx="5" cy="5" r="5"/><path d="M0 5h10M5 0c-2 2.5-2 7.5 0 10M5 0c2 2.5 2 7.5 0 10" stroke="#fff" stroke-width=".7" fill="none"/></symbol>
</svg>

<main class="sheet">
  <section class="card card--front">
    <div class="brand">
      <div class="brand__name"><span class="brand__mark"></span>Harbor Quill</div>
      <p class="brand__tagline">Multilingual Web Content and Language Services...</p>
    </div>
    <div class="divider"></div>
    <div class="contact">
      <p><span class="contact__name">Your Name</span> <span class="contact__title">/ Title</span></p>
      <ul class="contact__list">
        <li class="contact__item"><svg class="contact__icon"><use href="#icon-phone"/></svg>123-456-7890</li>
        <li class="contact__item"><svg class="contact__icon"><use href="#icon-mobile"/></svg>123-456-7890</li>
        <li class="contact__item"><svg class="contact__icon"><use href="#icon-fax"/></svg>123-456-7890</li>
        <li class="contact__item"><svg class="contact__icon"><use href="#icon-mail"/></svg>name@website.com</li>
        <li class="contact__item"><svg class="contact__icon"><use href="#icon-web"/></svg>www.website.com</li>
      </ul>
      <p class="contact__address">Complex name, Street<br>City, State, zip code</p>
    </div>
    <p class="fine-print">xxxxxxxxxxxxxxxxxxxxxxxxxxxxxxxxxxxxxxxxxxxxxxxxxx</p>
  </section>

  <section class="card card--back">
    <div class="brand">
      <div class="brand__name"><span class="brand__mark"></span>Harbor Quill</div>
      <p class="brand__tagline">Multilingual Web Content and Language Services...</p>
    </div>
    <div class="divider"></div>
    <div class="contact">
      <p><span class="contact__name">Your Name</span> <span class="contact__title">/ Title</span></p>
      <ul class="contact__list">
        <li class="contact__item"><svg class="contact__icon"><use href="#icon-phone"/></svg>123-456-7890</li>
        <li class="contact__item"><svg class="contact__icon"><use href="#icon-mobile"/></svg>123-456-7890</li>
        <li class="contact__item"><svg class="contact__icon"><use href="#icon-fax"/></svg>123-456-7890</li>
        <li class="contact__item"><svg class="contact__icon"><use href="#icon-mail"/></svg>name@website.com</li>
        <li class="contact__item"><svg class="contact__icon"><use href="#icon-web"/></svg>www.website.com</li>
      </ul>
      <p class="contact__address">Complex name, Street<br>City, State, zip code</p>
    </div>
    <p class="fine-print">xxxxxxxxxxxxxxxxxxxxxxxxxxxxxxxxxxxxxxxxxxxxxxxxxx</p>
  </section>
</main>
</body>
</html>
```